Stationery Design Project

We need a stationery design for our Norwegian trucking company. We have existed for about 15 years and our 12 drivers uses relatively new vehicles to transport goods around in northern Norway. Long distance routes with fresh fish og food transport is our main operations.

We have already made alogo that's printed on our trucks. The logo and a picture of our trucks is attached. I think the logo i crappy, but since its already in use, changing it is not an option in this round. Still using a better colour scheme in the overall stationery and more interesting fonts is possible (altso in the logo).

Company details:
Name: Kjelvraket AS
Organisation nr 873 615 309
Post adress: 8642 Raudvik

I like minimalism and simplicity. I am avalibly for questions in normal GMT working hours either here or on mail: ivar@fjordlast.no

Reason: Hi. Im extending the deadline because I needed some time to find a vector file of our logo. Sorry for the inconvenience

Hi, and thanks for all your interest in the project. Some updates:

-          I have decided to commit to using one of the designs. Some designer will get the payment.

-          I have extended the deadline with 24 hours since I needed some time to find our firms vector logo (a slow Swedish man was holding me up)

-          We will not choose a design before the deadline. No need to rush.

-          We have received a lot of great design and think there is a need to specified the product we want to make:

o   Business Card for all our employers. I just need the design and will duplicate with the correct numbers and name myself. The information on should be: Logo, employer’s name, Phone number, email, website, Postal number and address. Use this as a template: logo, Leif Brattvoll, 47382066, Leif@fjordlast.no,, fjordlast.no, 8642 Raudvik. The order and placement of the information is your creative decision.

o   Stickers to put on the goods we travel. On the sticker the should be the following information: Logo, phone number, Tekst and link: Fraktæ av Kjelvraket. Ke du syns? Fjordlast.no/tilbakemelding (this means: Handled by Kjelvraket. What do you think Fjordlast.no/feedback -à the link will be a feedback form). The placement the information and size is your creative decision with some stings: we have been thinking of using Drukko for printing and see that a size about 6x6 cm, 8x5 or something like that. (with 3000 copies our budget is 200 punds). Any suggestions of other suppliers are welcome. Drukko price calculator http://www.drukkolabelhouse.co.uk/digital-litho-printing/printing-labels-tags/stickers/

o   Letterhead with logo, address, phone number and organizational number.

o   Envelopes with logo,address, phone number and organizational number.

Have a nice day.

 

 

• Using the blue colour in the logo and using a similar graphic approch.

```html
<!DOCTYPE html>
<html lang="no">
<head>
<meta charset="utf-8">
<title>Kjelvraket – visittkort</title>
<link rel="stylesheet" href="https://fonts.googleapis.com/css2?family=Source+Sans+3:wght@400;600;700&display=swap">
<style>
  :root {
    --backdrop: #b9bcc0;
    --paper: #ffffff;
    --brand-deep: #0b4fa2;
    --brand-mid: #0a72ba;
    --brand-light: #2a8ad0;
    --ink: #2f3033;
    --ink-soft: #6c6e72;
    --rule: #c9cbce;
  }
  * { box-sizing: border-box; margin: 0; padding: 0; }
  html, body { width: 1200px; height: 751px; overflow: hidden; }
  body {
    position: relative;
    background: var(--backdrop);
    font-family: "Source Sans 3", "Myriad Pro", Arial, sans-serif;
    color: var(--ink);
  }
  .card {
    position: absolute;
    width: 524px;
    height: 298px;
    border-radius: 18px;
    overflow: hidden;
  }
  .card--front { left: 64px; top: 52px; background: var(--paper); }
  .card--back-deep { left: 620px; top: 52px; background: var(--brand-deep); }
  .card--back-white { left: 64px; top: 393px; height: 299px; background: var(--paper); border: 1px solid #555; }
  .card--back-mid { left: 620px; top: 393px; height: 299px; background: var(--brand-mid); }

  .wordmark {
    position: absolute;
    left: 0; right: 0;
    display: flex;
    align-items: center;
    justify-content: center;
    gap: 14px;
    font-weight: 700;
    font-size: 48px;
    letter-spacing: 0.5px;
  }
  .wordmark__dot { width: 18px; height: 18px; border-radius: 50%; }
  .card--front .wordmark { top: 98px; color: var(--brand-deep); }
  .card--front .wordmark__dot { background: var(--brand-deep); }
  .card--back-deep .wordmark, .card--back-mid .wordmark { top: 128px; color: #fff; }
  .card--back-deep .wordmark__dot, .card--back-mid .wordmark__dot { background: #fff; }
  .card--back-white .wordmark { top: 128px; color: var(--brand-deep); }
  .card--back-white .wordmark__dot { background: var(--brand-deep); }

  .website {
    position: absolute;
    left: 0; right: 0;
    text-align: center;
    font-size: 17px;
    letter-spacing: 4px;
  }
  .card--back-deep .website, .card--back-mid .website { top: 248px; color: #fff; }
  .card--back-white .website { top: 248px; color: var(--ink); }

  .holder {
    position: absolute;
    right: 281px;
    top: 166px;
    text-align: right;
  }
  .holder__name { font-size: 19px; font-weight: 700; color: var(--brand-deep); line-height: 24px; }
  .holder__address { font-size: 16px; line-height: 22px; display: flex; align-items: center; justify-content: flex-end; gap: 5px; }
  .divider {
    position: absolute;
    left: 256px; top: 154px;
    width: 1px; height: 70px;
    background: var(--rule);
  }
  .contact {
    position: absolute;
    left: 269px;
    top: 156px;
    font-size: 16px;
    line-height: 23.5px;
  }
  .contact__line { display: flex; align-items: center; gap: 5px; }
  .contact__label { color: var(--brand-mid); }
  .icon { width: 11px; height: 11px; fill: var(--brand-deep); }

  .wave { position: absolute; left: 0; bottom: 0; width: 524px; height: 80px; }
  .card--front .website {
    left: 29px; right: auto;
    top: 264px;
    text-align: left;
    color: #fff;
    font-size: 16px;
  }
</style>
</head>
<body>

  <section class="card card--front" aria-label="Visittkort forside">
    <div class="wordmark"><span class="wordmark__dot"></span>Kjelvraket</div>

    <div class="holder">
      <p class="holder__name">Leif Brattvoll</p>
      <p class="holder__address">
        <svg class="icon" viewBox="0 0 12 12" aria-hidden="true"><path d="M1 6 6 1.5 11 6V11H1Z"/></svg>
        8642 Raudvik
      </p>
    </div>

    <div class="divider"></div>

    <div class="contact">
      <p class="contact__line">
        <svg class="icon" viewBox="0 0 12 12" aria-hidden="true"><path d="M2.5 1h2l1 3-1.3 1a6.5 6.5 0 0 0 2.8 2.8l1-1.3 3 1v2a1.5 1.5 0 0 1-1.5 1.5A9.5 9.5 0 0 1 1 2.5 1.5 1.5 0 0 1 2.5 1Z"/></svg>
        47382066
      </p>
      <p class="contact__line"><span class="contact__label">Org nr</span> 873 615 309</p>
      <p class="contact__line">
        <svg class="icon" viewBox="0 0 12 12" aria-hidden="true"><path d="M1 3h10v7H1Zm1 1 4 3 4-3"/></svg>
        Leif@fjordlast.no
      </p>
    </div>

    <svg class="wave" viewBox="0 0 524 80" aria-hidden="true">
      <path d="M0 10C130 0 230 20 300 40 380 62 450 45 524 20V80H0Z" fill="var(--brand-light)"/>
      <path d="M0 22C130 12 230 34 300 52 380 74 450 58 524 34V80H0Z" fill="#fff"/>
      <path d="M0 28C130 20 230 40 300 58 380 78 450 64 524 40V80H0Z" fill="var(--brand-deep)"/>
    </svg>
    <p class="website">www.fjordlast.no</p>
  </section>

  <section class="card card--back-deep" aria-label="Visittkort bakside, mørk blå">
    <div class="wordmark"><span class="wordmark__dot"></span>Kjelvraket</div>
    <p class="website">www.fjordlast.no</p>
  </section>

  <section class="card card--back-white" aria-label="Visittkort bakside, hvit">
    <div class="wordmark"><span class="wordmark__dot"></span>Kjelvraket</div>
    <p class="website">www.fjordlast.no</p>
  </section>

  <section class="card card--back-mid" aria-label="Visittkort bakside, blå">
    <div class="wordmark"><span class="wordmark__dot"></span>Kjelvraket</div>
    <p class="website">www.fjordlast.no</p>
  </section>

</body>
</html>
```